KRV Business Card

Looking for a business card for my restaurant group I own. Four different concepts:

Copperfield Alehouse
Bristow Alehouse
Tanager's Stone Hearth Kitchen
Pellston Patty Company

Card doesn't need to include all the logos.

```html
<!DOCTYPE html>
<html lang="en">
<head>
<meta charset="utf-8">
<title>KRV Business Card</title>
<link href="https://fonts.googleapis.com/css2?family=Lato:wght@400;700&family=Montserrat:wght@600&display=swap" rel="stylesheet">
<style>
  :root {
    --backdrop: #484848;
    --gold: #d1af6d;
    --paper: #ffffff;
    --ink: #1f1f1f;
  }
  * { margin: 0; padding: 0; box-sizing: border-box; }
  html, body { width: 1200px; height: 900px; overflow: hidden; }
  body {
    background: var(--backdrop);
    position: relative;
    font-family: "Lato", sans-serif;
  }
  .card {
    position: absolute;
    top: 200px;
    width: 310px;
    height: 502px;
  }
  .card-front {
    left: 253px;
    background: var(--paper);
    border-radius: 56px 0 56px 0;
  }
  .card-back {
    left: 627px;
    background: var(--gold);
    border-radius: 0 56px 0 56px;
    color: var(--paper);
  }
  .brand {
    position: absolute;
    left: 0;
    width: 100%;
    text-align: center;
    font-family: "Lato", sans-serif;
    font-weight: 700;
  }
  .brand-initials {
    display: block;
    font-size: 56px;
    line-height: 56px;
    letter-spacing: 2px;
  }
  .brand-name {
    display: block;
    margin-top: 18px;
    font-size: 15px;
    letter-spacing: 3px;
  }
  .card-front .brand { top: 104px; color: var(--gold); }
  .card-back .brand { top: 170px; color: var(--paper); }

  .contact {
    position: absolute;
    left: 35px;
    top: 326px;
    color: var(--ink);
    font-size: 14px;
  }
  .contact-name {
    font-family: "Montserrat", sans-serif;
    font-weight: 600;
    font-size: 18px;
    color: var(--gold);
    line-height: 22px;
    letter-spacing: 0.3px;
  }
  .contact-role { line-height: 18px; }
  .contact-list { list-style: none; margin-top: 6px; }
  .contact-list li {
    display: flex;
    align-items: center;
    gap: 5px;
    line-height: 18.5px;
  }
  .contact-list svg { width: 11px; height: 11px; fill: var(--gold); }
  .contact-address { margin-top: 7px; margin-left: -3px; line-height: 18px; }

  .venues {
    position: absolute;
    top: 395px;
    width: 100%;
    list-style: none;
    text-align: center;
    font-weight: 700;
    font-size: 12.5px;
    line-height: 16px;
    text-transform: uppercase;
  }
</style>
</head>
<body>
  <section class="card card-front">
    <div class="brand">
      <span class="brand-initials">KRV</span>
      <span class="brand-name">KESTREL RIDGE VENTURES</span>
    </div>
    <div class="contact">
      <p class="contact-name">DANIEL HARLOW</p>
      <p class="contact-role">Managing Director</p>
      <ul class="contact-list">
        <li><svg viewBox="0 0 12 12"><path d="M1 4c0-2 2-3 5-3s5 1 5 3l-2 1-1-2H4L3 5zM3 6h6l1 5H2z"/></svg>044-555 018 274</li>
        <li><svg viewBox="0 0 12 12"><path d="M1 2h10v8H1zM1.8 3v.6L6 6.6l4.2-3V3L6 5.8z" fill-rule="evenodd"/></svg>hello@kestrelridge.com</li>
        <li><svg viewBox="0 0 12 12"><circle cx="6" cy="6" r="5"/></svg>www.kestrelridge.com</li>
      </ul>
      <p class="contact-address">12345, Address Goes Here<br>Country Name, 123456</p>
    </div>
  </section>

  <section class="card card-back">
    <div class="brand">
      <span class="brand-initials">KRV</span>
      <span class="brand-name">KESTREL RIDGE VENTURES</span>
    </div>
    <ul class="venues">
      <li>Copperfield Alehouse</li>
      <li>Bristow Alehouse</li>
      <li>Tanager's Stone Hearth Kitchen</li>
      <li>Pellston Patty Company</li>
    </ul>
  </section>
</body>
</html>
```